Small legal and financial translation company needs Squarespace website, brochure and logo

Hello,
We are Lumarin Services (www.lumarinservices-example.com), a boutique legal and financial translation company. We offer our services mainly to Spanish customers. Our primary line of business is the translation of financial statements, but we translate a wide variety legal and financial texts.
The project we are offering comprises three parts: a redo of the current website, an informational brochure for potential customer and a logo design. These three parts should provide a consistent image. We would develop content soon.
We are looking for a website that would look like a typical law firm website, nothing too fancy. Right now, it is in English, Spanish and French, although the new site need only be in English and Spanish. There must be good toggling between the English and Spanish versions. There would be no need for tie-ins to social media and it would not contain a blog. Basically, a static site. We aren't interesting in driving traffic to the site or SEO, as we will contact nearly all potential customers beforehand. The website must be built in Squarespace to enable a smooth transition. The content would be similar to the current page, we'll be working on the exact content, but a rough draft is attached.
The brochure will be some three pages and would introduce the company to potential customers, using similar images as the website and the logo to be designed.
The only specifications for the logo is, as the website and brochure, it convey a sense of security and trust.
Feel free to ask with any questions as this is the first time we have used this platform.
Thank you!
Updates

I've added a more or less final version for the text in the brochure and updated the brief. Added Wednesday, June 10, 2015

Target Market(s)

Spanish law firms, auditors, accountants, banks, investment firms

Industry/Entity Type

Finance

Logo Text

Lumarin Services

Number of Pages Required

5+ page

Font styles to use
Serif

Requirements
Must have
• The website must be built in Squarespace and have a good option to toggle between English and Spanish versions.
• Brochure must be in both English and Spanish, I'm attaching a rough draft of the information that it will probably have. This should give an idea about what to include and the spacing. I will update it to include the final information.
Nice to have
• Would be nice to have some quality finance- and legal-related images
Should not have
• Vibrant colours

```html
<!DOCTYPE html>
<html lang="en">
<head>
<meta charset="utf-8">
<title>Lumarin Services — Translation Specialist</title>
<link href="https://fonts.googleapis.com/css2?family=EB+Garamond:ital,wght@0,400;0,600;1,400&family=Montserrat:wght@400;700&display=swap" rel="stylesheet">
<style>
  :root {
    --ink: #333333;
    --text-grey: #7a7a7a;
    --text-strong: #555555;
    --white: #ffffff;
    --logo-blue: #a8dcef;
    --teal: #2fb3a3;
    --heading-teal: #1f7f93;
    --photo-light: #bdbdbd;
    --photo-mid: #8a8a8a;
    --photo-dark: #3c3c3c;
  }
  * { margin: 0; padding: 0; box-sizing: border-box; }
  html, body { width: 1200px; height: 1024px; overflow: hidden; background: var(--white); }
  body { position: relative; font-family: "EB Garamond", Georgia, serif; color: var(--ink); }

  .hero {
    position: absolute; left: 0; top: 0; width: 1200px; height: 549px;
  }
  .hero-photo {
    position: absolute; inset: 0;
    background: linear-gradient(180deg, var(--photo-light) 0%, #a5a5a5 22%, #6f6f6f 45%, #4a4a4a 70%, var(--photo-dark) 100%);
  }
  .brand {
    position: absolute; left: 18px; top: 30px;
    font-family: "EB Garamond", Georgia, serif; font-size: 28px; font-weight: 400;
    color: var(--logo-blue); letter-spacing: 0.5px;
  }
  .main-nav {
    position: absolute; top: 39px; right: 16px;
    display: flex; align-items: center;
    font-family: "Montserrat", Arial, sans-serif; font-size: 11px; font-weight: 700;
    letter-spacing: 1.2px; color: var(--white);
  }
  .main-nav a { color: inherit; text-decoration: none; margin-right: 24px; }
  .main-nav .nav-cta {
    margin: 0 0 0 0; width: 113px; height: 31px; line-height: 29px; text-align: center;
    border: 1.5px solid var(--white); border-radius: 16px;
  }
  .hero-eyebrow {
    position: absolute; top: 180px; left: 0; width: 100%; text-align: center;
    font-style: italic; font-size: 19px; color: var(--white);
  }
  .hero-title {
    position: absolute; top: 220px; left: 0; width: 100%; text-align: center;
    font-family: "Montserrat", Arial, sans-serif; font-weight: 700; font-size: 48px;
    line-height: 53px; letter-spacing: 2px; color: var(--white);
  }
  .hero-button {
    position: absolute; left: 537px; top: 349px; width: 126px; height: 33px;
    background: var(--teal); border-radius: 17px; color: var(--white);
    font-family: "Montserrat", Arial, sans-serif; font-weight: 700; font-size: 12px;
    letter-spacing: 1.2px; line-height: 33px; text-align: center;
  }

  .about-title {
    position: absolute; top: 570px; left: 0; width: 100%; text-align: center;
    font-size: 29px; font-weight: 400; color: var(--ink);
  }
  .about-text {
    position: absolute; top: 638px; left: 292px; width: 668px; text-align: center;
    font-size: 16.5px; line-height: 25px; color: var(--text-grey);
  }
  .about-text strong { color: var(--text-strong); font-weight: 600; }

  .fact-card {
    position: absolute; top: 834px; width: 226px; height: 148px; overflow: hidden;
  }
  .fact-photo { position: absolute; inset: 0; }
  .fact-band {
    position: absolute; left: 0; width: 100%;
    background: rgba(255, 255, 255, 0.72); text-align: center;
  }
  .fact-figure { color: var(--heading-teal); font-size: 27px; line-height: 28px; }
  .fact-caption { color: var(--ink); font-size: 14px; line-height: 14px; }
  .card-years { left: 243px; }
  .card-years .fact-photo { background: linear-gradient(180deg, #cfcfcf 0%, #8e8e8e 55%, #4d4d4d 100%); }
  .card-years .fact-band { top: 50px; height: 60px; padding-top: 6px; }
  .card-words { left: 487px; }
  .card-words .fact-photo { background: linear-gradient(180deg, #dadada 0%, #7d7d7d 50%, #3a3a3a 100%); }
  .card-words .fact-band { top: 46px; height: 64px; padding-top: 6px; }
  .card-words .fact-caption { margin-top: 6px; }
  .card-clients { left: 731px; }
  .card-clients .fact-photo { background: linear-gradient(180deg, #9a9a9a 0%, #b5b5b5 50%, #5a5a5a 100%); }
  .card-clients .fact-band { top: 36px; height: 88px; padding-top: 2px; }
  .card-clients .fact-figure { font-size: 25px; line-height: 28px; }
  .card-clients .fact-caption { font-size: 13.5px; line-height: 14px; padding: 0 16px; }
</style>
</head>
<body>
  <header class="hero">
    <div class="hero-photo" role="img" aria-label="Black and white aerial photograph of a dense city skyline with skyscrapers"></div>
    <div class="brand">Lumarin Services</div>
    <nav class="main-nav">
      <a href="#">HOME</a>
      <a href="#">ABOUT</a>
      <a href="#">NEWS</a>
      <a href="#">READ ME</a>
      <a href="#" class="nav-cta">TAKE ACTION</a>
    </nav>
    <p class="hero-eyebrow">Trust</p>
    <h1 class="hero-title">TRANSLATION<br>SPECIALIST</h1>
    <a class="hero-button">LEARN MORE</a>
  </header>

  <section class="about">
    <h2 class="about-title">Who we are</h2>
    <p class="about-text">We are a small, highly qualified group of professionals with <strong>backgrounds in law, financial services and translation</strong> that boasts experience in global consulting and auditing firms, law firms and companies from a <strong>wide cross-section of industries</strong>. Sensitive to the workings of the world of finance, accounting and law, we are <strong>detail-oriented experts</strong> striving to facilitate understanding among investors, companies and international organisations:</p>
  </section>

  <div class="fact-card card-years">
    <div class="fact-photo" role="img" aria-label="Black and white photograph of office towers seen from below"></div>
    <div class="fact-band">
      <div class="fact-figure">over 30 years</div>
      <div class="fact-caption">of combined experience</div>
    </div>
  </div>
  <div class="fact-card card-words">
    <div class="fact-photo" role="img" aria-label="Black and white photograph of a glass skyscraper seen from below"></div>
    <div class="fact-band">
      <div class="fact-figure">over a milion</div>
      <div class="fact-caption">words translated annually</div>
    </div>
  </div>
  <div class="fact-card card-clients">
    <div class="fact-photo" role="img" aria-label="Black and white photograph of a city street with sunlight between buildings"></div>
    <div class="fact-band">
      <div class="fact-figure">serving</div>
      <div class="fact-caption">Big 4 firms, leading international law firms and banks and MERIDEX 40 listings and blue chips</div>
    </div>
  </div>
</body>
</html>
```